Aunt Roula's Bakery

I am about to create a luxury boutique that specializes in cake baking and cupcake
and ready for parties and special events and order delivery
the logo has already made

Boutique

Email:auntroulasbakery@mailbox-example.net
Instagram: aunt_roula_bakery
Twitter: xxxxxxx
WhatsApp: xxxxxxx

Requirements
Must have
• luxury design

```html
<!DOCTYPE html>
<html lang="en">
<head>
<meta charset="utf-8">
<title>Aunt Roula's Bakery – Business Card</title>
<link rel="stylesheet" href="https://fonts.googleapis.com/css2?family=Alegreya+Sans:wght@400&display=swap">
<style>
  :root {
    --page-bg: #ece9e6;
    --card-bg: #ffffff;
    --ink-grey: #7b7a72;
    --rose: #d99aac;
    --divider: #cfccc6;
  }
  html, body {
    margin: 0;
    padding: 0;
    width: 1200px;
    height: 902px;
    overflow: hidden;
    background: var(--page-bg);
    font-family: "Alegreya Sans", "Trebuchet MS", sans-serif;
  }
  .card {
    position: absolute;
    left: 80px;
    top: 155px;
    width: 1040px;
    height: 592px;
    background: var(--card-bg);
    border-radius: 30px;
    box-shadow: 0 6px 24px rgba(0, 0, 0, 0.12);
    overflow: hidden;
  }
  .brand {
    position: absolute;
    left: 50px;
    top: 137px;
    width: 400px;
    text-align: center;
  }
  .brand-dot {
    display: block;
    width: 116px;
    height: 116px;
    margin: 0 auto 26px;
    border-radius: 50%;
    background: var(--rose);
  }
  .brand-name {
    margin: 0;
    color: var(--ink-grey);
    font-size: 40px;
    font-weight: 400;
    line-height: 1.15;
    letter-spacing: 2px;
    text-transform: uppercase;
  }
  .divider {
    position: absolute;
    left: 490px;
    top: 139px;
    width: 2px;
    height: 314px;
    background: var(--divider);
  }
  .person {
    position: absolute;
    left: 530px;
    top: 136px;
  }
  .person-name {
    margin: 0;
    color: var(--ink-grey);
    font-size: 44px;
    font-weight: 400;
    line-height: 1;
  }
  .person-role {
    margin: 4px 0 0;
    color: var(--rose);
    font-size: 27px;
    line-height: 1;
  }
  .contacts {
    position: absolute;
    left: 530px;
    top: 270px;
    margin: 0;
    padding: 0;
    list-style: none;
  }
  .contact {
    display: flex;
    align-items: center;
    height: 34px;
    color: var(--ink-grey);
    font-size: 25px;
    line-height: 1;
    white-space: nowrap;
  }
  .contact-icon {
    width: 26px;
    height: 26px;
    margin-right: 16px;
    flex: none;
  }
</style>
</head>
<body>
  <main class="card">
    <div class="brand">
      <span class="brand-dot"></span>
      <p class="brand-name">Aunt Roula's<br>Bakery</p>
    </div>

    <div class="divider"></div>

    <div class="person">
      <p class="person-name">Mira Haddad</p>
      <p class="person-role">Owner</p>
    </div>

    <ul class="contacts">
      <li class="contact">
        <svg class="contact-icon" viewBox="0 0 28 28" aria-hidden="true">
          <rect width="28" height="28" rx="5" fill="var(--rose)"/>
          <path d="M7 11c0-3 14-3 14 0v2h-4v-2h-6v2H7z" fill="#fff"/>
          <rect x="8" y="14" width="12" height="8" rx="1.5" fill="#fff"/>
          <circle cx="14" cy="18" r="2" fill="var(--rose)"/>
        </svg>
        000-000-0000
      </li>
      <li class="contact">
        <svg class="contact-icon" viewBox="0 0 28 28" aria-hidden="true">
          <rect width="28" height="28" rx="5" fill="var(--rose)"/>
          <rect x="6" y="8" width="16" height="12" fill="none" stroke="#fff" stroke-width="1.8"/>
          <path d="M6 8l8 7 8-7" fill="none" stroke="#fff" stroke-width="1.8"/>
        </svg>
        auntroulasbakery@mailbox-example.net
      </li>
      <li class="contact">
        <svg class="contact-icon" viewBox="0 0 28 28" aria-hidden="true">
          <rect width="28" height="28" rx="5" fill="var(--rose)"/>
        </svg>
        aunt_roula_bakery
      </li>
      <li class="contact">
        <svg class="contact-icon" viewBox="0 0 28 28" aria-hidden="true">
          <rect width="28" height="28" rx="5" fill="var(--rose)"/>
        </svg>
        aunt_roula_bakery
      </li>
      <li class="contact">
        <svg class="contact-icon" viewBox="0 0 28 28" aria-hidden="true">
          <rect width="28" height="28" rx="5" fill="var(--rose)"/>
        </svg>
        aunt_roula_bakery
      </li>
    </ul>
  </main>
</body>
</html>
```